Our companies name is The Gilded Ladle and we specialize in craft cupcakes, what I mean by that is that we bake our cupcakes with craft beer and other alcoholic drinks. We are trying to focus on being elegant but at the same time unpretentious. Since we are incorporating beer in our cupcakes we want the business card to have our logo in the front and our information in the back.

Once we select the best design we will provide the contact information to be added. Thank you.

Industry/Entity Type

Business

Font styles to use
Decorative
Script

Requirements
Must have
• Round corners
Should not have
• Square corners

```html
<!DOCTYPE html>
<html lang="en">
<head>
<meta charset="utf-8">
<title>The Gilded Ladle — Business Card</title>
<link href="https://fonts.googleapis.com/css2?family=Rye&family=Arimo:wght@400;700&display=swap" rel="stylesheet">
<style>
  :root {
    --page: #e9e6e2;
    --card-white: #ffffff;
    --card-black: #0b0b0b;
    --accent-red: #c8242a;
    --text-light: #f2f2f2;
  }
  * { margin: 0; padding: 0; box-sizing: border-box; }
  html, body {
    width: 1200px; height: 848px; overflow: hidden;
    background: var(--page);
  }
  .sheet {
    width: 1200px; height: 848px;
    display: flex; flex-direction: column; align-items: center; justify-content: center;
    gap: 40px;
  }
  .card {
    width: 640px; height: 366px;
    border-radius: 22px;
    overflow: hidden;
    position: relative;
    box-shadow: 0 8px 22px rgba(0,0,0,0.22);
    background: var(--card-white);
  }

  /* Info side */
  .card--info { display: flex; }
  .info__brand {
    width: 43%;
    display: flex; align-items: center; justify-content: center; gap: 12px;
    border-right: 3px solid var(--card-black);
    position: relative;
  }
  .info__brand::after {
    content: ""; position: absolute; top: 0; right: 4px; bottom: 0;
    width: 6px; background: var(--card-white);
  }
  .info__details {
    flex: 1;
    background: var(--card-black);
    padding: 42px 22px 30px 36px;
    color: var(--text-light);
    font-family: "Arimo", Arial, sans-serif;
  }
  .employee-name {
    font-family: "Rye", Georgia, serif;
    font-weight: 400;
    color: var(--accent-red);
    font-size: 27px; letter-spacing: 0.5px;
    line-height: 1.05;
  }
  .employee-role { font-size: 14px; margin-top: 4px; }
  .contact-list { list-style: none; margin-top: 38px; }
  .contact-list li {
    display: flex; align-items: center; gap: 12px;
    font-size: 15px; line-height: 1.55;
  }
  .contact-list svg { width: 13px; height: 13px; flex: none; fill: var(--accent-red); }
  .address { margin-top: 30px; font-size: 15px; line-height: 1.35; white-space: nowrap; }

  /* Brand name lockup */
  .brand-dot {
    width: 22px; height: 22px; border-radius: 50%;
    background: var(--accent-red); flex: none;
  }
  .brand-name {
    font-family: "Arimo", Arial, sans-serif;
    font-weight: 700;
    color: var(--card-black);
    font-size: 24px; line-height: 1.15;
    text-align: center;
    text-transform: uppercase;
    letter-spacing: 1px;
  }

  /* Logo side */
  .card--logo { display: flex; align-items: center; justify-content: center; }
  .band {
    position: absolute; top: 0; bottom: 0; width: 46px;
    background: var(--card-black);
  }
  .band::after {
    content: ""; position: absolute; top: 0; bottom: 0; width: 2px;
    background: var(--card-white);
  }
  .band--left { left: 0; }
  .band--left::after { right: 8px; }
  .band--right { right: 0; }
  .band--right::after { left: 8px; }
  .card--logo .logo-lockup {
    display: flex; align-items: center; gap: 14px;
    margin-left: 110px;
  }
  .card--logo .brand-name { font-size: 26px; }
  .card--logo .brand-dot { width: 26px; height: 26px; }
</style>
</head>
<body>
<main class="sheet">

  <section class="card card--info" aria-label="Business card, contact side">
    <div class="info__brand">
      <span class="brand-dot" aria-hidden="true"></span>
      <span class="brand-name">The Gilded<br>Ladle</span>
    </div>
    <div class="info__details">
      <h1 class="employee-name">EMPLOYEE NAME</h1>
      <p class="employee-role">Managing Director</p>
      <ul class="contact-list">
        <li>
          <svg viewBox="0 0 16 16" aria-hidden="true"><path d="M3 1l3 3-1.5 2c1 2 3 4 5 5L11.5 9.5l3 3-2 2.5C6.5 14.5 1.5 9.5 1 3z"/></svg>
          (xxx) xxx-xxxx
        </li>
        <li>
          <svg viewBox="0 0 16 16" aria-hidden="true"><path d="M4 1h8v4H4zM1 6h14v6h-3v3H4v-3H1zM5 10v4h6v-4z"/></svg>
          xxx xxx xxxx
        </li>
        <li>
          <svg viewBox="0 0 16 16" aria-hidden="true"><path d="M8 1a7 7 0 100 14A7 7 0 008 1zm0 2c1 1 1.6 2.7 1.7 4H6.3C6.4 5.7 7 4 8 3zM6.3 9h3.4C9.6 10.3 9 12 8 13c-1-1-1.6-2.7-1.7-4z"/></svg>
          www.yourwebsit.com
        </li>
        <li>
          <svg viewBox="0 0 16 16" aria-hidden="true"><path d="M1 3h14v10H1zm1.5 1.5L8 9l5.5-4.5z"/></svg>
          info@youremail.com
        </li>
      </ul>
      <p class="address">Your Address Inc 2nd Lane Ave Edison,<br>NJ&nbsp;&nbsp;00000</p>
    </div>
  </section>

  <section class="card card--logo" aria-label="Business card, brand side">
    <span class="band band--left" aria-hidden="true"></span>
    <div class="logo-lockup">
      <span class="brand-dot" aria-hidden="true"></span>
      <span class="brand-name">The Gilded Ladle</span>
    </div>
    <span class="band band--right" aria-hidden="true"></span>
  </section>

</main>
</body>
</html>
```